Business Card Design Project

We need a Business Card for an Mechanical Engineering firm in Singapore. The design should be Modern & Technical looking, yet eye catching.

Our company deals in Cutting Tools & Machine Accessories for the Manufacturing Industries such as Oil & Gas, Aero Space, etc... For more information on our Company, you can either email me or view our website www.torvalen.com.sg.

We are trying to revamp our image to give our consumers a fresh new perspective to our company, so we welcome all ideas.

Industry/Entity Type

Business

Requirements
Must have
• Must incorporate New Company Logo into the card as shown in Uploaded file.

```html
<!DOCTYPE html>
<html lang="en">
<head>
<meta charset="utf-8">
<title>Torvalen Tools – Business Card</title>
<link rel="stylesheet" href="https://fonts.googleapis.com/css2?family=Open+Sans:wght@400;600&display=swap">
<style>
  :root {
    --bg: #d9d9d9;
    --card-dark: #231f20;
    --card-light: #ffffff;
    --brand-red: #9b1c22;
    --brand-red-deep: #7d1419;
    --ink: #2a2a2a;
    --paper-text: #f2f2f2;
  }
  * { box-sizing: border-box; margin: 0; padding: 0; }
  html, body { width: 1200px; height: 951px; overflow: hidden; }
  body {
    background: var(--bg);
    font-family: "Open Sans", Arial, sans-serif;
    position: relative;
  }
  .card {
    position: absolute;
    width: 560px;
    height: 320px;
    border-radius: 22px;
    overflow: hidden;
    box-shadow: 0 6px 18px rgba(0,0,0,0.25);
  }

  /* Back of card */
  .card-back {
    left: 90px; top: 90px;
    background: var(--card-dark);
    color: var(--paper-text);
  }
  .card-back .wordmark {
    position: absolute;
    left: 0; right: 0; top: 118px;
    display: flex; align-items: center; justify-content: center; gap: 14px;
  }
  .card-back .wordmark-dot {
    width: 26px; height: 26px; border-radius: 50%;
    background: var(--brand-red);
  }
  .card-back .wordmark-name {
    font-size: 38px; font-weight: 600; letter-spacing: 1px;
    color: var(--paper-text);
  }
  .card-back .website {
    position: absolute; left: 0; right: 0; top: 252px;
    text-align: center; font-size: 17px; letter-spacing: 0.5px;
  }

  /* Front of card */
  .card-front {
    left: 550px; top: 500px;
    background: var(--card-light);
    color: var(--ink);
  }
  .card-front .panel { position: absolute; inset: 0; }
  .card-front .wordmark {
    position: absolute; left: 40px; top: 64px;
    font-size: 23px; font-weight: 600; color: var(--brand-red);
    letter-spacing: 0.5px;
  }
  .contact {
    position: absolute; left: 30px; font-size: 14px; line-height: 19px;
    display: flex; gap: 8px;
  }
  .contact svg { flex: 0 0 14px; margin-top: 3px; }
  .contact-address { top: 150px; }
  .contact-list {
    position: absolute; left: 30px; top: 212px;
    list-style: none; font-size: 14px; line-height: 20px;
  }
  .contact-list li { display: flex; gap: 8px; align-items: center; }
  .contact-list .accent { color: var(--brand-red); }
  .person {
    position: absolute; right: 46px; top: 158px; text-align: right;
    color: var(--paper-text);
  }
  .person-name { font-size: 19px; }
  .person-role { font-size: 13px; margin-top: 2px; }
</style>
</head>
<body>

<section class="card card-back" aria-label="Card back">
  <div class="wordmark">
    <span class="wordmark-dot"></span>
    <span class="wordmark-name">TORVALEN TOOLS</span>
  </div>
  <p class="website">www.torvalentools.com</p>
</section>

<section class="card card-front" aria-label="Card front">
  <svg class="panel" viewBox="0 0 560 320" preserveAspectRatio="none" aria-hidden="true">
    <path d="M318 0 C272 110 282 220 330 320 L560 320 L560 0 Z" fill="#111"/>
    <path d="M336 0 C300 110 312 230 372 320 L560 320 L560 0 Z" fill="var(--brand-red)"/>
    <path d="M336 0 C300 110 312 230 372 320 L400 320 C345 230 330 110 360 0 Z" fill="var(--brand-red-deep)"/>
  </svg>

  <p class="wordmark">TORVALEN TOOLS</p>

  <div class="contact contact-address">
    <svg width="14" height="14" viewBox="0 0 14 14" aria-hidden="true">
      <path d="M7 1 L13 7 H11 V13 H3 V7 H1 Z" fill="var(--brand-red)"/>
    </svg>
    <p>4100 Kell Marin Rd.<br>Dalwick, TX 78114</p>
  </div>

  <ul class="contact-list">
    <li>
      <svg width="14" height="14" viewBox="0 0 14 14" aria-hidden="true">
        <path d="M3 1 L5.5 1 L6.5 4 L5 5.2 C5.8 7 7 8.2 8.8 9 L10 7.5 L13 8.5 V11 C13 12 12 13 11 13 C5.5 13 1 8.5 1 3 C1 2 2 1 3 1 Z" fill="var(--brand-red)"/>
      </svg>
      <span>512-004-2710</span>
    </li>
    <li>
      <svg width="14" height="14" viewBox="0 0 14 14" aria-hidden="true">
        <rect x="4" y="1" width="6" height="12" rx="1.2" fill="var(--brand-red)"/>
        <rect x="5.2" y="2.6" width="3.6" height="7" fill="#fff"/>
      </svg>
      <span>512-004-2711</span>
    </li>
    <li>
      <svg width="14" height="14" viewBox="0 0 14 14" aria-hidden="true">
        <rect x="1" y="3" width="12" height="9" rx="1" fill="var(--brand-red)"/>
        <path d="M1.5 3.5 L7 8 L12.5 3.5" stroke="#fff" stroke-width="1.2" fill="none"/>
      </svg>
      <span>info@torvalentools.com</span>
    </li>
    <li>
      <svg width="14" height="14" viewBox="0 0 14 14" aria-hidden="true">
        <circle cx="7" cy="7" r="6" fill="var(--brand-red)"/>
      </svg>
      <span>www.<span class="accent">torvalentools</span>.com</span>
    </li>
  </ul>

  <div class="person">
    <p class="person-name">Marcus Elvery</p>
    <p class="person-role">director</p>
  </div>
</section>

</body>
</html>
```